Backup Software Tri-fold Brochure Project

We need a great looking and informative brochure to describe our new Backup Software offering. The brochures are to be used in retail and small business environments given to clients interested in protecting their computer from data loss.
The brochure should include attractive imagery that conveys a sense of Trust and Security to the prospective client.
The copy is provided as an attachment to this project. We'd like our Brisk Harbor product logo to be printed on the back cover. The logo is attached to this project.
The finished tri-fold brochure will be submitted to Loomcraft for printing as an 8.5" x 11" tri-fold brochure. Their design instructions are online http://loomcraft-example.com/custom-brochures.aspx.
The finished product should be Adobe Illustrator CS3 (*.ai) with a PDF Proof.
Target Market(s)
Retail and Small Business customers
Industry/Entity Type
Software
Colors
Designer to choose colors to be used in the design.
Look and feel

```html
<!DOCTYPE html>
<html lang="en">
<head>
<meta charset="utf-8">
<title>Brisk Harbor Offsite Backup – Tri-fold Brochure</title>
<link href="https://fonts.googleapis.com/css2?family=Lato:wght@400;700&family=Roboto+Condensed:wght@700;900&display=swap" rel="stylesheet">
<style>
:root{
  --green:#5fae3b;
  --green-dark:#4a9a2c;
  --blue:#1560a8;
  --blue-deep:#1a5ea8;
  --ink:#2b2b2b;
  --grey-text:#3a3a3a;
  --footer:#2f2f31;
  --paper:#ffffff;
  --bg:#ffffff;
}
*{box-sizing:border-box;margin:0;padding:0}
html,body{width:1200px;height:972px;overflow:hidden;background:var(--bg)}
body{position:relative;font-family:"Lato",sans-serif;color:var(--ink)}
.spread{position:absolute;left:318px;width:566px;background:var(--paper);box-shadow:0 3px 8px rgba(0,0,0,.35);overflow:hidden}
.spread--outside{top:38px;height:442px}
.spread--inside{top:492px;height:441px}
.panel{position:absolute;top:0;height:100%;overflow:hidden}
.p1{left:0;width:192px}
.p2{left:192px;width:181px}
.p3{left:373px;width:193px}
.shape{position:absolute;left:0;top:0;width:100%;height:100%}
.footer-bar{position:absolute;left:0;bottom:0;width:100%;height:24px;background:var(--footer);color:#e6e6e6;font-size:5px;text-align:center;line-height:24px;white-space:nowrap}
.heading{font-family:"Roboto Condensed",sans-serif;font-weight:700;text-transform:uppercase;color:var(--blue)}
.tiny{font-size:4.7px;line-height:6.6px;text-align:justify;color:var(--grey-text)}
.tiny p{margin-bottom:6px}
.tiny .heading{font-size:7px;line-height:8px;margin:16px 0 8px}
.tiny--white{color:#fff}
.tiny--white .heading{color:#fff;font-size:7px;margin:0 0 6px}
.tiny--white ul{list-style:none;margin-bottom:6px}
.tiny--white li{padding-left:16px;margin-bottom:6px;position:relative}
.tiny--white li::before{content:"";position:absolute;left:3px;top:2px;width:2px;height:2px;background:#fff;border-radius:50%}
.photo{position:absolute}
.brand{font-family:"Lato",sans-serif;font-weight:700;color:var(--green);white-space:nowrap;display:flex;align-items:center;gap:6px}
.brand .mark{width:14px;height:14px;background:var(--green)}
.copyright{position:absolute;left:0;width:100%;top:396px;text-align:center;font-size:5px;color:#555}
.headline{position:absolute;left:0;width:100%;text-align:center;font-family:"Roboto Condensed",sans-serif;font-weight:900}
.headline .l1{display:block;font-size:17px;color:#222}
.headline .l2{display:block;font-size:16px;color:var(--green);margin-top:3px}
.headline .l3{display:block;font-size:64px;color:var(--blue);line-height:60px;letter-spacing:-1px;margin-top:2px}
.body{font-size:7.9px;line-height:9.9px;text-align:justify;color:var(--grey-text)}
.body p{margin-bottom:10px}
.body .heading{font-size:7.5px;margin-bottom:9px}
.options-list{list-style:none;font-size:7.9px;line-height:9.9px;color:var(--grey-text)}
.options-list li{position:relative;padding-left:13px;margin-bottom:10px;text-align:justify}
.options-list li::before{content:"";position:absolute;left:1px;top:3px;width:4px;height:4px;background:var(--blue);border-radius:50%}
</style>
</head>
<body>

<section class="spread spread--outside" aria-label="Brochure outside">
  <div class="panel p1">
    <div class="tiny" style="position:absolute;left:11px;top:16px;width:171px">
      <p>Your computer stores everything you've ever created. Everything you've written, every email you've sent, every list you've made, every picture you've taken or movie you've made, all music you've created, your proposals, your spreadsheets, your presentations, your word files, your artwork, programs you've written, anything you've dictated, and much more... All your digital life is stored on your computer and is at risk of loss without backup.</p>
      <p>And your computer stores a copy of all your personal information. Your passwords, your online banking, your PINs, your credit cards and all your health and shopping records. This makes it a juicy target for hackers. Every day your digital life is exposed to computer Viruses, Malware and spammers all trying to break in. If they succeed the damage could be incalculable.</p>
      <p>If hackers destroy your information or a simple hard drive failure happens, restoring your programs will cost you days of effort and potentially hundreds of dollars. But your files could be unrecoverable. This means the loss of everything you've ever created.</p>
      <p>The only protection is a great backup.</p>
      <div class="heading">We have what you need</div>
      <p>We can create a snapshot of all the programs and files on your computer using our Image Backup technology. We'll give you your backup on an external hard drive which you can store someplace safe. If anything happens, just bring in your computer and your Image Backup and we'll restore your computer back to the point when the snapshot was taken.</p>
      <p>Restoring from an Image Backup is like setting your computer back in time. To make sure all your new files are protected, we'll also install Tidewell Systems' Brisk Harbor software to backup your files every night. These backups are stored in Tidewell Systems' secure datacenter to protect you from even the most severe data loss scenarios.</p>
      <p>The combination of your Image Backup and your nightly backup will ensure you have complete protection for both your programs and your files. It means complete peace of mind.</p>
    </div>
    <div class="photo" role="img" aria-label="Photo of illuminated server racks in a data center" style="left:0;top:300px;width:192px;height:118px;background:linear-gradient(180deg,rgba(255,255,255,0) 0%,#9aa3b8 30%,#2a3250 65%,#151a2e 100%)"></div>
    <div class="footer-bar">www.netwatch-example.org/reports/2016_report.pdf</div>
  </div>

  <div class="panel p2">
    <svg class="shape" viewBox="0 0 181 442" preserveAspectRatio="none" aria-hidden="true">
      <defs><linearGradient id="g2" x1="0" y1="0" x2="0" y2="1"><stop offset="0" stop-color="#ffffff"/><stop offset="1" stop-color="#e9e9e9"/></linearGradient></defs>
      <rect width="181" height="442" fill="url(#g2)"/>
      <polygon points="0,0 181,0 181,352 0,302" fill="#5fae3b"/>
    </svg>
    <div class="tiny tiny--white" style="position:absolute;left:12px;top:17px;width:159px">
      <div class="heading">What to do</div>
      <p>Call us to schedule a day to bring in your computer.<br>OR<br>Once a month we do "Image Backup Saturday". Drop off your computer in the morning and pick it up a few hours later. Call for a copy of our schedule.</p>
      <div class="heading">Options</div>
      <p>Our Image Backup technology can protect</p>
      <ul>
        <li>Kestrel OS PC's and Laptops running Kestrel OS 7 and above (Kestrel OS 8, 10+)</li>
        <li>Kestrel OS Servers running Kestrel OS 2008 and above (Kestrel OS 2012, 2016+)</li>
      </ul>
      <div class="heading" style="margin-top:12px">How it works</div>
      <p>Our technology is designed to take advantage of the powerful imaging technology embedded in Kestrel OS. Deep within the core of the OS is an imaging engine that can create a point-in-time backup of the Kestrel OS Operating System, device drivers, programs and system state. The backup can be used later to recover the system back to this point-in-time.</p>
      <p>Backups created by our Imaging technology can even be used to restore Kestrel OS to dissimilar hardware. This is a quick way to migrate to a new computer without having to reinstall everything from scratch.</p>
      <p>Our technology stores backups as Kestrel Soft "Virtual Hard Disk" (VHD). These VHD files can be directly mounted from the Kestrel OS Disk Manager. This is a great way to browse the contents of your Image Backup and restore individual files and folders.</p>
    </div>
    <div class="brand" style="position:absolute;left:14px;top:362px;font-size:20px">
      <span class="mark"></span>Brisk Harbor
    </div>
    <div class="copyright">Copyright(c) 2017, Tidewell Systems, Inc. All Rights Reserved</div>
    <div class="footer-bar">research.driveindex-example.com/disk_failures.pdf</div>
  </div>

  <div class="panel p3">
    <svg class="shape" viewBox="0 0 193 442" preserveAspectRatio="none" aria-hidden="true">
      <defs><linearGradient id="g3" x1="0" y1="0" x2="0" y2="1"><stop offset="0" stop-color="#ffffff"/><stop offset="1" stop-color="#e6e6e6"/></linearGradient></defs>
      <rect width="193" height="442" fill="url(#g3)"/>
    </svg>
    <svg class="shape" viewBox="0 0 193 442" preserveAspectRatio="none" role="img" aria-label="Photo of a businessman's hands cupped around a glowing shield with a padlock">
      <defs><linearGradient id="gp" x1="0" y1="0" x2="1" y2="1"><stop offset="0" stop-color="#8d9196"/><stop offset=".5" stop-color="#b9bdc1"/><stop offset="1" stop-color="#6e7378"/></linearGradient></defs>
      <polygon points="0,0 193,0 193,296 0,354" fill="url(#gp)"/>
      <polyline points="0,354 193,296" fill="none" stroke="#5fae3b" stroke-width="2.5"/>
    </svg>
    <div class="headline" style="top:308px">
      <span class="l1">Your entire</span>
      <span class="l2">Digital Life is at</span>
      <span class="l3">RISK</span>
    </div>
    <div class="footer-bar">www.laptopstudy-example.com/lost_laptop_study.pdf</div>
  </div>
</section>

<section class="spread spread--inside" aria-label="Brochure inside">
  <div class="panel p1">
    <svg class="shape" viewBox="0 0 192 441" preserveAspectRatio="none" aria-hidden="true">
      <defs><linearGradient id="g4" x1="0" y1="0" x2="0" y2="1"><stop offset="0" stop-color="#ffffff"/><stop offset="1" stop-color="#ececec"/></linearGradient></defs>
      <rect width="192" height="441" fill="url(#g4)"/>
      <polygon points="0,0 192,0 192,136 0,90" fill="#5fae3b"/>
      <polyline points="0,90 192,136" fill="none" stroke="#1560a8" stroke-width="2"/>
    </svg>
    <div class="brand" style="position:absolute;left:22px;top:40px;font-size:19px;color:#7cbd5e">
      <span class="mark" style="background:#7cbd5e"></span>Brisk Harbor
    </div>
    <div class="body" style="position:absolute;left:19px;top:138px;width:156px">
      <div class="heading">We have what you need</div>
      <p>We can create a snapshot of all the programs and files on your computer using our Image Backup technology. We'll give you your backup on an external hard drive which you can store someplace safe. If anything happens, just bring in your computer and your Image Backup and we'll restore your computer back to the point when the snapshot was taken.</p>
      <p>Restoring from an Image Backup is like setting your computer back in time. To make sure all your new files are protected, we'll also install Tidewell Systems' Brisk Harbor software to backup your files every night. These backups are stored in Tidewell Systems' secure datacenter to protect you from even the most severe data loss scenarios.</p>
      <p>The combination of your Image Backup and your nightly backup will ensure you have complete protection for both your programs and your files. It means complete peace of mind.</p>
    </div>
    <div class="footer-bar" style="height:23px;line-height:23px">www.netwatch-example.org/reports/2016_report.pdf</div>
  </div>

  <div class="panel p2">
    <svg class="shape" viewBox="0 0 181 441" preserveAspectRatio="none" aria-hidden="true">
      <rect width="181" height="441" fill="#ffffff"/>
      <polygon points="0,312 181,262 181,270 0,320" fill="#5fae3b"/>
      <polygon points="0,320 181,270 181,441 0,441" fill="#1a5ea8"/>
    </svg>
    <div class="photo" role="img" aria-label="Photo of a man holding a laptop in a data center, surrounded by floating digital screens" style="left:0;top:0;width:181px;height:140px;background:linear-gradient(180deg,#9fb4c8 0%,#c9d6e2 55%,#ffffff 100%)"></div>
    <div class="body" style="position:absolute;left:19px;top:148px;width:152px">
      <div class="heading">Options</div>
      <p style="color:var(--blue);font-weight:700;text-align:left;margin-bottom:7px">Our Image Backup technology<br>can protect</p>
      <ul class="options-list">
        <li>Kestrel OS PC's and Laptops running Kestrel OS 7 and above (Kestrel OS 8, 10+)</li>
        <li>Kestrel OS Servers running Kestrel OS 2008 and above (Kestrel OS 2012, 2016+)</li>
      </ul>
    </div>
    <div style="position:absolute;left:0;top:316px;width:100%;text-align:center;color:#fff">
      <div class="heading" style="color:var(--green);font-size:7.5px;margin-bottom:6px">What to do</div>
      <div style="font-size:11.5px;line-height:14px">Call us to schedule a day<br>to bring in your computer</div>
      <div style="font-size:8px;margin:6px 0">OR</div>
      <div style="font-size:8px;line-height:10px;padding:0 14px">Once a month we do "Image Backup Saturday". Drop off your computer in the morning and pick it up a few hours later. Call for a copy of our schedule.</div>
    </div>
  </div>

  <div class="panel p3">
    <svg class="shape" viewBox="0 0 193 441" preserveAspectRatio="none" aria-hidden="true">
      <defs><linearGradient id="g5" x1="0" y1="0" x2="0" y2="1"><stop offset="0" stop-color="#ffffff"/><stop offset="1" stop-color="#f0f0f0"/></linearGradient></defs>
      <rect width="193" height="441" fill="url(#g5)"/>
    </svg>
    <div class="photo" role="img" aria-label="Photo of clasped hands in warm sunlight" style="left:0;top:318px;width:193px;height:123px;background:linear-gradient(135deg,#f4f4f4 0%,#f1e3b0 45%,#d9a56a 75%,#b87a45 100%)"></div>
    <div class="body" style="position:absolute;left:26px;top:30px;width:142px">
      <div class="heading" style="margin-bottom:11px">How it works</div>
      <p>Our technology is designed to take advantage of the powerful imaging technology embedded in Kestrel OS. Deep within the core of the OS is an imaging engine that can create a point-in-time backup of the Kestrel OS Operating System, device drivers, programs and system state. The backup can be used later to recover the system back to this point-in-time.</p>
      <p>Backups created by our Imaging technology can even be used to restore Kestrel OS to dissimilar hardware. This is a quick way to migrate to a new computer without having to reinstall everything from scratch.</p>
      <p>Our technology stores backups as Kestrel Soft "Virtual Hard Disk" (VHD). These VHD files can be directly mounted from the Kestrel OS Disk Manager. This is a great way to browse the contents of your Image Backup and restore individual files and folders.</p>
    </div>
  </div>
</section>

</body>
</html>
```